Harrow Hide Revival Product Label

We need a design for a label to be used on bottles of leather cleaner and conditioner products that will be used in curated kits. We would like it to incorporate our business logo as well as have an area that we can fill in later with the appropriate product name as needed. We would like to see designs that use shades of brown, but we are open to other colors often seen in leather. I am including the Harrow Hide business Logo below, however again we would prefer to have the label in various shades of browns, rather than the red and grey, more like the mock-up that I am also attaching.

*** I am attaching examples of the types of bottles that will be used. They vary in size from 8 oz to 16 oz. if you are designing a label for a spray bottle they are from 16-32 oz. ***

```html
<!DOCTYPE html>
<html lang="en">
<head>
<meta charset="utf-8">
<title>Harrow Hide Revival – Leather Cleaner Label</title>
<link rel="stylesheet" href="https://fonts.googleapis.com/css2?family=Cinzel:wght@400;500&family=Oswald:wght@500&family=Saira+Semi+Condensed:ital,wght@1,500;1,600&display=swap">
<style>
  :root {
    --backdrop: #a7b1bd;
    --label-white: #ffffff;
    --band-top: #5c1a1a;
    --band-bottom: #361010;
    --gold: #d2aa55;
    --gold-light: #f4dc8a;
    --copper-top: #a8693c;
    --copper-bottom: #8a5330;
    --copper-text: #f4dcc0;
    --ink: #2a1410;
    --tagline: #6a2c12;
    --bullet-text: #ffffff;
  }
  * { box-sizing: border-box; margin: 0; padding: 0; }
  html, body { width: 1200px; height: 833px; overflow: hidden; }
  body {
    background: var(--backdrop);
    position: relative;
    font-family: "Saira Semi Condensed", "Arial Narrow", sans-serif;
  }
  .label {
    position: absolute;
    left: 365px; top: 44px;
    width: 470px; height: 745px;
    background: var(--label-white);
    border-radius: 26px;
    overflow: hidden;
    box-shadow: 0 6px 24px rgba(40, 50, 65, 0.25);
  }
  .label-art { position: absolute; inset: 0; }
  .brand-plaque {
    position: absolute;
    left: 102px; top: 85px;
    width: 266px; height: 100px;
    padding: 0 22px;
    display: flex; align-items: center; justify-content: center; gap: 10px;
  }
  .brand-dot {
    width: 24px; height: 24px; border-radius: 50%;
    background: var(--copper-text);
    flex: none;
  }
  .brand-name {
    color: var(--copper-text);
    font-weight: 600;
    font-style: italic;
    line-height: 1;
    text-transform: uppercase;
    white-space: nowrap;
  }
  .brand-name .main { display: block; font-size: 24px; letter-spacing: 0.3px; }
  .brand-name .sub { display: block; font-size: 9px; letter-spacing: 1.2px; margin-top: 4px; }
  .product-title {
    position: absolute;
    left: 0; right: 0; top: 300px;
    text-align: center;
    font-family: "Cinzel", serif;
    color: var(--label-white);
    font-size: 66px;
    font-weight: 500;
    line-height: 1;
    letter-spacing: -1px;
  }
  .product-subtitle {
    position: absolute;
    left: 39px; width: 392px; top: 363px; height: 40px;
    text-align: center;
    font-family: "Cinzel", serif;
    color: var(--ink);
    font-size: 32px;
    line-height: 40px;
    letter-spacing: 13px;
    padding-left: 13px;
  }
  .features {
    position: absolute;
    left: 28px; top: 490px; right: 28px;
    list-style: none;
    color: var(--bullet-text);
    font-style: italic;
    font-weight: 600;
    font-size: 17px;
    line-height: 25px;
    white-space: nowrap;
  }
  .features li { display: flex; align-items: center; gap: 8px; }
  .features li::before {
    content: ""; width: 8px; height: 8px; border-radius: 50%;
    border: 2px solid var(--bullet-text); flex: none;
  }
  .volume {
    position: absolute; left: 0; right: 0; top: 668px;
    text-align: center;
    font-family: "Oswald", sans-serif;
    font-weight: 500;
    font-size: 22px;
    color: var(--ink);
    line-height: 1;
  }
  .tagline {
    position: absolute; left: 0; right: 0; top: 697px;
    text-align: center;
    font-style: italic; font-weight: 500;
    font-size: 20px;
    color: var(--tagline);
    line-height: 1;
  }
</style>
</head>
<body>
  <div class="label">
    <svg class="label-art" width="470" height="745" viewBox="0 0 470 745" aria-hidden="true">
      <defs>
        <linearGradient id="band" x1="0" y1="0" x2="0" y2="1">
          <stop offset="0" stop-color="var(--band-top)"/>
          <stop offset="1" stop-color="var(--band-bottom)"/>
        </linearGradient>
        <linearGradient id="goldLine" x1="0" y1="0" x2="1" y2="0">
          <stop offset="0" stop-color="var(--gold)"/>
          <stop offset="0.5" stop-color="var(--gold-light)"/>
          <stop offset="1" stop-color="var(--gold)"/>
        </linearGradient>
        <linearGradient id="copper" x1="0" y1="0" x2="0" y2="1">
          <stop offset="0" stop-color="var(--copper-top)"/>
          <stop offset="1" stop-color="var(--copper-bottom)"/>
        </linearGradient>
        <linearGradient id="rule" x1="0" y1="0" x2="1" y2="0">
          <stop offset="0" stop-color="var(--gold)" stop-opacity="0"/>
          <stop offset="0.5" stop-color="var(--gold)"/>
          <stop offset="1" stop-color="var(--gold)" stop-opacity="0"/>
        </linearGradient>
      </defs>
      <path d="M0 150 Q235 100 470 150 L470 623 Q235 660 0 623 Z" fill="url(#band)"/>
      <path d="M0 150 Q235 100 470 150" fill="none" stroke="url(#goldLine)" stroke-width="4"/>
      <path d="M0 623 Q235 660 470 623" fill="none" stroke="url(#goldLine)" stroke-width="4"/>
      <path d="M102 85 L368 85 L368 184 Q235 194 102 184 Z" fill="url(#copper)"/>
      <path d="M102 184 Q235 194 368 184" fill="none" stroke="url(#goldLine)" stroke-width="3"/>
      <rect x="50" y="290" width="370" height="1.5" fill="url(#rule)"/>
      <rect x="50" y="420" width="370" height="1.5" fill="url(#rule)"/>
      <path d="M39 344 L11 350 L22 366 L11 382 L39 400 Z" fill="var(--label-white)"/>
      <path d="M431 344 L459 350 L448 366 L459 382 L431 400 Z" fill="var(--label-white)"/>
      <rect x="39" y="362" width="392" height="42" fill="var(--label-white)" stroke="var(--band-bottom)" stroke-width="2"/>
    </svg>

    <div class="brand-plaque">
      <span class="brand-dot"></span>
      <span class="brand-name"><span class="main">Harrow Hide</span><span class="sub">Revival</span></span>
    </div>

    <h1 class="product-title">LEATHER</h1>
    <p class="product-subtitle">CLEANER</p>

    <ul class="features">
      <li>Thick, rich lotion</li>
      <li>Leaves a non-poly, natural, soft, supple finish</li>
      <li>Pleasant fragrance</li>
    </ul>

    <p class="volume">16 US FL. OZ 473 ML</p>
    <p class="tagline">pH Balanced Superior Cleaner</p>
  </div>
</body>
</html>
```